Diverse, up-scale salon needs eye-catching, unique business cards.

We are looking for a unique business card design for our stylist but that can also be multi functional and used for appointment reminder and referrals. I will need a design in a format that I can modify names and titles going forward. In the past we have had a dark background with the logo on one side, and stylist and contact information on the other but we are open to all ideas. I have included our mission statement as well as branded colors below. The statement doesn't need to go on the card, it's just a reference for target market. We need space for the stylists name, title, instagram handle and then the salons phone number, website and address. I am also open to adding a spot for a qr code linked to the stylist instagram or the salon booking link.

primary brand colors:
#333333 #233415 #36502a #93874a #000000
Mission statement:
Vessolin Hair Studio, a high-end salon located in the lively Downtown Farmington, Michigan, is committed to providing exceptional services in a welcoming and relaxed environment to meet the needs of our diverse clientele.
Our salon specializes in contemporary custom haircuts, coloring, extensions, and barbering and beard grooming services. Our team of skilled stylists is passionate and inventive in their hair styling techniques. At the heart of our salon are values centered on quality, innovation, creativity, and above all, comfort. These core values are evident in every appointment across our customizable array of services.
Our goal is to establish a benchmark for exceptional hair care for every human.
Website: www.vessolinhairstudio.example
instagram: @vessolinhairstudio
address: 41782 Pelham Crest Rd, Farmington MI
phone: 248-613-4087

Industry/Entity Type

Hair Salon

Contact Information for Business Card

Stylist name, title, phone, instagram, website, address, (optional qr code)

Requirements
Should not have
• Does not need mission statement on the card.

```html
<!DOCTYPE html>
<html lang="en">
<head>
<meta charset="utf-8">
<title>Vessolin Hair Studio – Business Card</title>
<link href="https://fonts.googleapis.com/css2?family=Montserrat:wght@400;700&display=swap" rel="stylesheet">
<style>
  :root {
    --backdrop: #dcdcd8;
    --paper: #ffffff;
    --olive: #93874a;
    --olive-deep: #8a7f44;
    --olive-light: #c9bb72;
    --ink: #555555;
  }
  * { margin: 0; padding: 0; box-sizing: border-box; }
  html, body {
    width: 1200px; height: 801px; overflow: hidden;
    background: var(--backdrop);
    font-family: "Montserrat", sans-serif;
  }
  .card {
    position: absolute; top: 252px;
    width: 520px; height: 297px;
    box-shadow: 0 6px 18px rgba(0,0,0,.18);
    overflow: hidden;
  }
  .card--front { left: 60px; background: var(--paper); }
  .card--back { left: 620px; background: var(--olive); }

  .front__tab {
    position: absolute; left: 0; top: 196px;
    width: 14px; height: 26px;
    background: var(--olive); border-radius: 0 8px 8px 0;
  }
  .stylist { position: absolute; left: 42px; top: 170px; }
  .stylist__name {
    font-weight: 700; font-size: 19px; letter-spacing: .5px;
    color: var(--olive); text-transform: uppercase;
  }
  .stylist__title { font-size: 12px; color: var(--ink); margin-top: 2px; }

  .contact {
    position: absolute; left: 300px; top: 168px;
    font-size: 12px; color: var(--ink); line-height: 1.45;
  }
  .contact__address { margin-bottom: 12px; }
  .contact__row { display: flex; align-items: center; gap: 7px; }
  .contact__icon { width: 10px; height: 10px; flex: none; }

  .brand {
    position: absolute; display: flex; align-items: center; gap: 14px;
  }
  .card--front .brand { right: 36px; top: 48px; }
  .card--back .brand { left: 50%; top: 50%; transform: translate(-50%, -50%); }
  .brand__ring { width: 60px; height: 60px; border-radius: 50%; border: 3px solid currentColor; flex: none; }
  .brand__name {
    font-weight: 700; font-size: 18px; letter-spacing: 2px;
    text-transform: uppercase; line-height: 1.25;
  }
  .card--front .brand { color: var(--olive); }
  .card--back .brand { color: var(--olive-light); }
</style>
</head>
<body>
  <section class="card card--front" aria-label="Business card front">
    <div class="brand">
      <span class="brand__ring"></span>
      <span class="brand__name">Vessolin<br>Hair Studio</span>
    </div>
    <span class="front__tab"></span>
    <div class="stylist">
      <p class="stylist__name">Marisa Dunholt</p>
      <p class="stylist__title">President</p>
    </div>
    <div class="contact">
      <p class="contact__address">41782 Pelham Crest Rd<br>Farmington MI</p>
      <p class="contact__row">
        <svg class="contact__icon" viewBox="0 0 10 10" aria-hidden="true"><path d="M2 1 L4 3 L3 4 Q4 6 6 7 L7 6 L9 8 L8 9 Q3 9 1 2 Z" fill="#93874a"/></svg>
        248-613-4087
      </p>
      <p class="contact__row">
        <svg class="contact__icon" viewBox="0 0 10 10" aria-hidden="true"><circle cx="5" cy="5" r="4" fill="none" stroke="#93874a" stroke-width="1.4"/></svg>
        @vessolinhairstudio
      </p>
      <p class="contact__row">
        <svg class="contact__icon" viewBox="0 0 10 10" aria-hidden="true"><circle cx="5" cy="5" r="4.5" fill="#93874a"/></svg>
        www.vessolinhairstudio.example
      </p>
    </div>
  </section>

  <section class="card card--back" aria-label="Business card back">
    <div class="brand">
      <span class="brand__ring"></span>
      <span class="brand__name">Vessolin<br>Hair Studio</span>
    </div>
  </section>
</body>
</html>
```